Corvane Paintless Dent Removal

Our company works on vehicles removing dents using a highly skilled trade which the metal is massaged out with special tools without disturbing the original paint, hence paintless dent removal. Besides keeping the paint and metal original its also very environmentally friendly since no paint or toxic fillers are used. Also we we are one of the most experienced companies in the business with 25 years

Target Market(s)

Retail Automobile consumers, Auto Dealerships and Auto Body Shops

Industry/Entity Type

Auto Repair

Contact Information for Business Card

Dale Hollister
PO Box 518 Brookmere, NY 11962
631-555-0148
corvanepdr@mailbox-example.com
website corvanepdr.example
youtube corvane paintless dent removal
25 years of experience removing Dents, Dings and Hail Damage

Font styles to use
Serif
Sans Serif

Colors

Designer to choose colors to be used in the design.

Requirements
Must have
• I do like things that are simple but classy and somewhat bold, also I like my logo so that should be somewhat important

```html
<!DOCTYPE html>
<html lang="en">
<head>
<meta charset="utf-8">
<title>Corvane Paintless Dent Removal – Business Card</title>
<link rel="stylesheet" href="https://fonts.googleapis.com/css2?family=Roboto:wght@400;700&family=Roboto+Condensed:wght@500;700&display=swap">
<style>
  :root {
    --backdrop: #2c2c2c;
    --card-white: #f2f2f2;
    --navy: #13294b;
    --lime: #7dc511;
    --text-gray: #555555;
    --divider: #b9b9b9;
    --gold: #d9a933;
    --gold-dark: #1d1a14;
    --white: #ffffff;
  }
  * { box-sizing: border-box; margin: 0; padding: 0; }
  html, body {
    width: 1200px; height: 960px; overflow: hidden;
    background: var(--backdrop);
    font-family: "Roboto", Arial, sans-serif;
  }
  .canvas { position: relative; width: 1200px; height: 960px; }

  .card {
    position: absolute; width: 600px; height: 342px; overflow: hidden;
  }

  /* Front */
  .card-front { left: 314px; top: 113px; background: var(--card-white); }
  .band { position: absolute; }
  .band-top { right: 0; top: 0; width: 326px; height: 17px; }
  .band-bottom { left: 0; bottom: 0; width: 318px; height: 17px; }

  .front-brand {
    position: absolute; left: 38px; top: 132px; width: 250px;
    display: flex; align-items: center; gap: 10px;
    color: var(--navy);
    font-family: "Roboto Condensed", Arial, sans-serif; font-weight: 700;
    font-size: 15px; line-height: 1.15; text-transform: uppercase;
  }
  .brand-dot { width: 34px; height: 34px; border-radius: 50%; background: var(--lime); flex: none; }
  .brand-name .big { display: block; font-size: 30px; letter-spacing: 0.5px; }

  .divider {
    position: absolute; left: 308px; top: 97px; width: 2px; height: 155px;
    background: linear-gradient(to bottom, transparent, var(--divider) 20%, var(--divider) 80%, transparent);
  }

  .contact { position: absolute; left: 332px; top: 94px; }
  .contact-name {
    font-family: "Roboto Condensed", Arial, sans-serif; font-weight: 700;
    font-size: 21px; color: var(--navy); text-transform: uppercase; letter-spacing: 0.2px;
  }
  .contact-address { margin-top: 8px; font-size: 14px; line-height: 19px; color: var(--text-gray); }
  .contact-list { list-style: none; margin-top: 6px; }
  .contact-list li {
    display: flex; align-items: center; gap: 9px;
    font-size: 14px; line-height: 19px; color: var(--text-gray);
  }
  .contact-list svg { width: 14px; height: 14px; flex: none; fill: var(--navy); }
  .contact-list .square-mark { width: 14px; height: 10px; background: var(--navy); border-radius: 2px; flex: none; }

  /* Back */
  .card-back { left: 311px; top: 472px; background: var(--lime); }
  .years-seal {
    position: absolute; left: 18px; top: 15px; width: 76px; height: 76px; border-radius: 50%;
    background: var(--gold-dark); border: 5px solid var(--gold);
    display: flex; flex-direction: column; align-items: center; justify-content: center;
    color: var(--gold); font-family: "Roboto Condensed", Arial, sans-serif; font-weight: 700;
  }
  .years-seal .num { font-size: 26px; line-height: 24px; }
  .years-seal .label { font-size: 9px; letter-spacing: 0.5px; }

  .back-brand {
    position: absolute; left: 0; right: 0; top: 130px;
    display: flex; justify-content: center; align-items: center;
    color: var(--white); text-align: center;
    font-family: "Roboto Condensed", Arial, sans-serif; font-weight: 700;
    font-size: 20px; line-height: 1.1; text-transform: uppercase;
  }
  .back-brand .big { display: block; font-size: 42px; letter-spacing: 1px; }

  .back-url {
    position: absolute; left: 0; right: 0; top: 280px; text-align: center;
    color: var(--white); font-size: 14px; letter-spacing: 5px;
  }
</style>
</head>
<body>
<div class="canvas">

  <section class="card card-front">
    <svg class="band band-top" viewBox="0 0 326 17" preserveAspectRatio="none" aria-hidden="true">
      <polygon points="0,0 326,0 326,17 17,17" fill="var(--navy)"/>
    </svg>
    <svg class="band band-bottom" viewBox="0 0 318 17" preserveAspectRatio="none" aria-hidden="true">
      <polygon points="0,0 301,0 318,17 0,17" fill="var(--navy)"/>
    </svg>

    <div class="front-brand">
      <span class="brand-dot"></span>
      <span class="brand-name"><span class="big">Corvane</span>Paintless Dent Removal</span>
    </div>

    <div class="divider"></div>

    <div class="contact">
      <h1 class="contact-name">Dale Hollister</h1>
      <p class="contact-address">PO Box 518<br>Brookmere, NY 11962</p>
      <ul class="contact-list">
        <li>
          <svg viewBox="0 0 24 24" aria-hidden="true"><path d="M6.6 10.8a15.1 15.1 0 0 0 6.6 6.6l2.2-2.2c.3-.3.7-.4 1-.2 1.1.4 2.3.6 3.6.6.6 0 1 .4 1 1V20c0 .6-.4 1-1 1C10.6 21 3 13.4 3 4c0-.6.4-1 1-1h3.5c.6 0 1 .4 1 1 0 1.3.2 2.5.6 3.6.1.3 0 .7-.2 1z"/></svg>
          631-555-0148
        </li>
        <li>
          <svg viewBox="0 0 24 24" aria-hidden="true"><path d="M2 5h20v14H2z M4 7v1l8 5 8-5V7l-8 5z" fill-rule="evenodd"/></svg>
          corvanepdr@mailbox-example.com
        </li>
        <li>
          <svg viewBox="0 0 24 24" aria-hidden="true"><path d="M12 2a10 10 0 1 0 0 20 10 10 0 0 0 0-20zm-1 17.9A8 8 0 0 1 4.1 10.9L9 15.8v1.1c0 1.1.9 2 2 2zm6.9-2.5c-.3-.8-1-1.4-1.9-1.4h-1v-3c0-.6-.4-1-1-1H8v-2h2c.6 0 1-.4 1-1V7h2c1.1 0 2-.9 2-2v-.4a8 8 0 0 1 2.9 12.8z"/></svg>
          corvanepdr.example
        </li>
        <li>
          <span class="square-mark"></span>
          corvane paintless dent removal
        </li>
      </ul>
    </div>
  </section>

  <section class="card card-back">
    <div class="years-seal">
      <span class="num">25</span>
      <span class="label">YEARS</span>
    </div>

    <div class="back-brand">
      <span><span class="big">Corvane</span>Paintless Dent Removal</span>
    </div>

    <p class="back-url">www.corvanepdr.example</p>
  </section>

</div>
</body>
</html>
```